Stylish business cards for KV7

To create an appealing and professional business card design for a WOMEN Owned Construction Supply Company.
2 sided card. Incorporate brand elements, curvy, colorful, sleek and bright. No solid white background. attached samples of styles added shapes/ribbons. Want something with that WOW that looks awesome, factor. It is a new logo, so feel free to mess with logo colors in the blue and teal factors that can look good with both dark and light background. If you want to try a watermark with just the KV7, without the "Supply" that might look cool to.

Industry/Entity Type

Women owned construction supply company

Contact Information for Business Card

Name, Title, and phone number and email, web page. maybe spot for qr code.

Font styles to use
Sans Serif

Requirements
Nice to have
• would love to see colors, maybe stylish ribbon dividers or some sort of 2 or 3 tone color card that compliments logo.
Should not have
• Please do not have all white background. Do not include Home/reale state/ or building images.

```html
<!DOCTYPE html>
<html lang="en">
<head>
<meta charset="UTF-8">
<title>KV7 Supply – Business Cards</title>
<link href="https://fonts.googleapis.com/css2?family=Poppins:wght@400;500;600&display=swap" rel="stylesheet">
<style>
  :root{
    --stage:#2b2b2d;
    --navy-deep:#1d3a5c;
    --navy:#2a4a6e;
    --slate:#5b7190;
    --teal:#2a9ec4;
    --teal-soft:#4ab0d4;
    --white:#ffffff;
    --ink:#1f3d63;
  }
  *{margin:0;padding:0;box-sizing:border-box}
  html,body{width:1200px;height:875px;overflow:hidden}
  body{
    background:var(--stage);
    font-family:"Poppins",sans-serif;
    position:relative;
  }
  .card{
    position:absolute;
    left:340px;
    width:520px;
    height:297px;
    border-radius:18px;
    overflow:hidden;
    box-shadow:0 18px 40px rgba(0,0,0,.45);
  }
  .card--front{
    top:95px;
    background:linear-gradient(115deg,var(--slate) 0%,var(--navy) 35%,var(--navy-deep) 100%);
    display:flex;align-items:center;justify-content:center;
  }
  .card--back{
    top:483px;
    background:linear-gradient(115deg,var(--slate) 0%,var(--navy) 55%,var(--navy-deep) 100%);
  }
  .brand-name{
    font-weight:600;
    font-size:52px;
    letter-spacing:1px;
    color:var(--white);
  }
  .card--back .brand-name{
    position:absolute;
    right:34px;top:92px;
    font-size:36px;
    color:var(--ink);
  }
  .back-shape{position:absolute;inset:0;width:100%;height:100%}
  .contact{
    position:absolute;left:34px;bottom:30px;
    color:var(--white);
  }
  .contact__name{
    color:var(--teal-soft);
    font-weight:600;font-size:17px;letter-spacing:.5px;
    text-transform:uppercase;line-height:1.1;
  }
  .contact__title{font-size:12px;margin-bottom:12px}
  .contact__address{font-size:12px;line-height:1.35;margin-bottom:12px}
  .contact__list{list-style:none;font-size:12px;line-height:1.55}
  .contact__list li{display:flex;align-items:center;gap:8px}
  .contact__list svg{width:11px;height:11px;flex:none}
</style>
</head>
<body>

<section class="card card--front" aria-label="Business card front">
  <span class="brand-name">KV7 Supply</span>
</section>

<section class="card card--back" aria-label="Business card back">
  <svg class="back-shape" viewBox="0 0 520 297" aria-hidden="true">
    <path class="ribbon" d="M253.5 145 A256 256 0 0 0 515 278 L513 264 A248 248 0 0 1 253.5 145 Z" fill="var(--teal)"/>
    <circle class="white-panel" cx="470" cy="20" r="240" fill="var(--white)"/>
  </svg>
  <span class="brand-name">KV7 Supply</span>

  <div class="contact">
    <p class="contact__name">Daniel Harper</p>
    <p class="contact__title">General Manager</p>
    <p class="contact__address">48 Lakeview Commons<br>Dover, NJ 07801 USA</p>
    <ul class="contact__list">
      <li>
        <svg viewBox="0 0 12 12"><path d="M2 1h2.5l1 2.5-1.3 1a6 6 0 0 0 3.3 3.3l1-1.3 2.5 1V11A9 9 0 0 1 1 2z" fill="var(--teal-soft)"/></svg>
        +1.555.010.274
      </li>
      <li>
        <svg viewBox="0 0 12 12"><rect x="1" y="2.5" width="10" height="7" rx="1" fill="var(--teal-soft)"/><path d="M1.5 3l4.5 3.5L10.5 3" fill="none" stroke="var(--navy)" stroke-width="1"/></svg>
        name@kv7supply.com
      </li>
      <li>
        <svg viewBox="0 0 12 12"><circle cx="6" cy="6" r="5" fill="none" stroke="var(--teal-soft)" stroke-width="1.3"/><path d="M1 6h10M6 1c2.5 2.8 2.5 7.2 0 10M6 1c-2.5 2.8-2.5 7.2 0 10" fill="none" stroke="var(--teal-soft)" stroke-width="1"/></svg>
        www.kv7supply.com
      </li>
    </ul>
  </div>
</section>

</body>
</html>
```